Roofing Contractor business card redesign

I want to redesign my business card with a fresh, eye catching concept

Target Market(s)

Residential Roofing Clients, potential employees, and subcontractors.

Industry/Entity Type

Business

Colors

Designer to choose colors to be used in the design.

Requirements
Nice to have
• I just want something that's more pleasing to the eye. You can use a combination of either / or of my logos.

```html
<!DOCTYPE html>
<html lang="en">
<head>
<meta charset="utf-8">
<title>Sound Crew General Contractors – Business Card</title>
<link rel="stylesheet" href="https://fonts.googleapis.com/css2?family=Source+Sans+3:wght@400;600;700&display=swap">
<style>
  :root {
    --stage: #000000;
    --card-yellow-top: #f8ee24;
    --card-yellow-bottom: #f6c414;
    --card-white: #ffffff;
    --ink: #2a1a0d;
    --brand: #4a1713;
    --art-dark: #4a2a1c;
    --art-mid: #e07a2a;
    --art-light: #f4d54a;
    --divider: rgba(120, 80, 20, 0.35);
  }
  * { margin: 0; padding: 0; box-sizing: border-box; }
  html, body {
    width: 1200px; height: 900px; overflow: hidden;
    background: var(--stage);
    font-family: "Source Sans 3", "Myriad Pro", sans-serif;
  }
  .stage { position: relative; width: 1200px; height: 900px; }
  .card {
    position: absolute; top: 271px; width: 457px; height: 281px;
    border-radius: 14px; overflow: hidden;
  }
  .card--front {
    left: 137px;
    background: linear-gradient(to bottom, var(--card-yellow-top), var(--card-yellow-bottom));
  }
  .card--back { left: 626px; background: var(--card-white); }

  .crew-art {
    position: absolute; left: 40px; top: 66px; width: 150px; height: 150px;
    border-radius: 50%;
    border: 4px solid #fff;
    background: radial-gradient(circle at 50% 40%, var(--art-light) 0%, var(--art-mid) 45%, var(--art-dark) 80%);
    box-shadow: 0 0 0 2px var(--art-dark);
  }
  .divider {
    position: absolute; left: 215px; top: 68px; width: 1px; height: 150px;
    background: var(--divider);
  }
  .contact { position: absolute; left: 240px; top: 40px; color: var(--ink); }
  .contact__name { font-size: 17px; font-weight: 700; line-height: 22px; margin-left: 1px; }
  .contact__title { font-size: 13px; line-height: 19px; }
  .contact__address { margin-top: 14px; font-size: 13px; line-height: 19px; }
  .contact__list { list-style: none; margin-top: 14px; }
  .contact__item {
    display: flex; align-items: center; gap: 7px;
    font-size: 13px; line-height: 19px;
  }
  .contact__item svg { width: 11px; height: 11px; fill: var(--ink); flex: none; }

  .brand {
    position: absolute; left: 0; right: 0; top: 100px;
    text-align: center; color: var(--brand); font-weight: 700;
  }
  .brand__name {
    display: inline-flex; align-items: center; gap: 12px;
    font-size: 50px; line-height: 54px; letter-spacing: -0.5px;
  }
  .brand__dot {
    width: 44px; height: 44px; border-radius: 50%; background: var(--brand);
  }
  .brand__sub { font-size: 23px; line-height: 30px; margin-top: 4px; }
</style>
</head>
<body>
<main class="stage">
  <section class="card card--front">
    <div class="crew-art" role="img" aria-label="Illustrated round emblem of three roofing workers holding tools"></div>
    <div class="divider"></div>
    <div class="contact">
      <p class="contact__name">Ray Kessler</p>
      <p class="contact__title">Tarrow Certified Roof Inspector</p>
      <p class="contact__title">Licensed Property Adjuster</p>
      <p class="contact__address">4180 Elmcrest Drive Suite 110<br>Plano, TX 75093</p>
      <ul class="contact__list">
        <li class="contact__item">
          <svg viewBox="0 0 24 24" aria-hidden="true"><path d="M6.6 10.8a15 15 0 0 0 6.6 6.6l2.2-2.2a1 1 0 0 1 1-.25 11.4 11.4 0 0 0 3.6.57 1 1 0 0 1 1 1V20a1 1 0 0 1-1 1A17 17 0 0 1 3 4a1 1 0 0 1 1-1h3.5a1 1 0 0 1 1 1c0 1.25.2 2.45.57 3.57a1 1 0 0 1-.25 1z"/></svg>
          (555) 318-2040
        </li>
        <li class="contact__item">
          <svg viewBox="0 0 24 24" aria-hidden="true"><path d="M7 1h10a2 2 0 0 1 2 2v18a2 2 0 0 1-2 2H7a2 2 0 0 1-2-2V3a2 2 0 0 1 2-2zm0 3v14h10V4zm5 15.5a1 1 0 1 0 0 2 1 1 0 0 0 0-2z"/></svg>
          (555) 627-9183
        </li>
        <li class="contact__item">
          <svg viewBox="0 0 24 24" aria-hidden="true"><path d="M2 5h20v14H2zm2 2v.5l8 5 8-5V7zm0 2.8V17h16V9.8l-8 5z"/></svg>
          ray@soundcrewtx.com
        </li>
        <li class="contact__item">
          <svg viewBox="0 0 24 24" aria-hidden="true"><path d="M12 2a10 10 0 1 0 0 20 10 10 0 0 0 0-20zm-1 17.9A8 8 0 0 1 4.1 10.1L9 15v1a2 2 0 0 0 2 2zm6.9-2.5A2 2 0 0 0 16 16h-1v-3a1 1 0 0 0-1-1H8v-2h2a1 1 0 0 0 1-1V7h2a2 2 0 0 0 2-2v-.4a8 8 0 0 1 2.9 12.8z"/></svg>
          SoundCrewGC.com
        </li>
      </ul>
    </div>
  </section>

  <section class="card card--back">
    <div class="brand">
      <p class="brand__name"><span class="brand__dot" aria-hidden="true"></span>Sound Crew</p>
      <p class="brand__sub">General Contractors, Inc.</p>
    </div>
  </section>
</main>
</body>
</html>
```